I have written a book called "Whispers from the Back Office - Uncover the trade tricks advisers bill huge fees every season for and would rather keep hidden"

This book will be sold through this webpage as an ebook. i have attached a copy of the cover of the book and I would like the website to be consistent with the look and feel of the book cover.

Target Market(s)

Business owners

Industry/Entity Type

Business

Requirements
Must have
• There has been a video produced for the promotion of this book which is yet to be completed. The video will be on ClipNest and the video needs to be prominent on the homepage.

I need to be able to manage and change the content as I wish on the website eg wordpress.

The page will need have a Coinvey purchase button

Also a 100% money back guarantee sign

Nice to have
• Friendloop plug in to show how many people like the page

Should not have
• I don't want the homepage or any of the other pages to be too cluttered

```html
<!DOCTYPE html>
<html lang="en">
<head>
<meta charset="utf-8">
<title>E-book – Whispers from the Back Office</title>
<link rel="stylesheet" href="https://fonts.googleapis.com/css2?family=Source+Sans+3:wght@400;600;700&display=swap">
<style>
  :root {
    --ink: #222222;
    --text: #3a3a3a;
    --header-bg: #f6f6f6;
    --frame-blue: #93defa;
    --panel-light: #f6f6f6;
    --panel-dark: #d6d6d6;
    --widget-bar: #4a6294;
    --link-blue: #3b5ea8;
    --footer-bg: #f2f2f2;
    --gold: #e7b20e;
    --gold-deep: #b47f06;
  }
  * { box-sizing: border-box; margin: 0; padding: 0; }
  html, body { width: 1200px; height: 1171px; overflow: hidden; background: #ffffff; }
  body { font-family: "Source Sans 3", "Helvetica Neue", Arial, sans-serif; color: var(--text); }
  .page { position: relative; width: 1200px; height: 1171px; overflow: hidden; background: #ffffff; }

  /* Header */
  .site-header { position: absolute; left: 0; top: 0; width: 1200px; height: 150px;
    background: linear-gradient(#fbfbfb, var(--header-bg)); }
  .brand { position: absolute; left: 83px; top: 34px; font-size: 54px; font-weight: 700;
    color: var(--ink); letter-spacing: -1px; line-height: 1; }
  .search { position: absolute; left: 861px; top: 26px; width: 258px; height: 33px;
    background: #ffffff; border: 1px solid #dddddd; }
  .search span { position: absolute; left: 12px; top: 7px; font-size: 13px; font-style: italic; color: #999999; }
  .search svg { position: absolute; right: 10px; top: 7px; }
  .main-nav { position: absolute; right: 86px; top: 82px; display: flex; align-items: center; }
  .main-nav a { font-size: 22px; color: #333333; text-decoration: none; padding: 0 23px; line-height: 1;
    border-left: 1px solid #c9c9c9; }
  .main-nav a:first-child { border-left: none; }
  .main-nav a:last-child { padding-right: 0; }

  /* Hero band */
  .hero { position: absolute; left: 0; top: 0; width: 1200px; height: 640px; }
  .hero-band { position: absolute; left: 0; top: 0; }
  .title-panel { position: absolute; left: 82px; top: 226px; width: 500px; height: 240px;
    background: linear-gradient(100deg, var(--panel-dark) 0%, var(--panel-light) 35%, var(--panel-dark) 100%);
    transform: rotate(-3deg); transform-origin: left top; padding: 40px 38px 0 38px;
    box-shadow: 0 6px 14px rgba(0, 0, 0, 0.12); }
  .title-panel .title-lead { font-size: 35px; font-weight: 400; color: #3a3a3a; line-height: 1.05; }
  .title-panel .title-main { font-size: 43px; font-weight: 700; color: #2d2d2d; line-height: 1.05; }
  .title-panel .title-sub { margin-top: 12px; font-size: 16.5px; line-height: 24px; color: #3a3a3a; }
  .video-frame { position: absolute; left: 659px; top: 203px; width: 465px; height: 331px;
    background: var(--frame-blue); padding: 10px; }
  .video-screen { position: relative; width: 445px; height: 311px; background: #ffffff; overflow: hidden; }
  .video-still { position: absolute; left: 110px; top: 14px; width: 235px; height: 297px;
    background: linear-gradient(#2a2a2a, #0c0c0c); border-radius: 90px 90px 6px 6px; }
  .play-button { position: absolute; left: 206px; top: 122px; }

  /* Main content */
  .intro { position: absolute; left: 82px; top: 662px; width: 690px; }
  .intro h1 { font-size: 28px; font-weight: 400; color: var(--ink); line-height: 1; letter-spacing: -0.2px; }
  .author-photo { position: absolute; left: 0; top: 45px; width: 173px; height: 174px;
    background: linear-gradient(135deg, #e9ecef 0%, #c8cdd2 45%, #5b6168 75%, #3a3e44 100%); }
  .intro-body { position: absolute; left: 191px; top: 43px; width: 500px; }
  .intro-body h2 { font-size: 22px; font-weight: 400; color: var(--ink); line-height: 1.2; margin-bottom: 6px; }
  .intro-body p, .intro-more { font-size: 15px; line-height: 22.5px; color: var(--text); }
  .intro-body p + p { margin-top: 4px; }
  .intro-more { position: absolute; left: 0; top: 230px; width: 700px; }

  /* Social widget */
  .like-box { position: absolute; left: 815px; top: 648px; width: 311px; height: 300px;
    border: 1px solid #aab4c8; background: #ffffff; font-size: 12px; }
  .like-box-head { height: 33px; background: var(--widget-bar); color: #ffffff; display: flex;
    align-items: center; padding: 0 12px 0 11px; font-size: 14px; font-weight: 400; }
  .like-page { display: flex; align-items: flex-start; padding: 10px 10px 0 6px; height: 64px;
    border-bottom: 1px solid #e3e3e3; margin: 0 6px; }
  .page-icon { width: 38px; height: 38px; background: #222222; border-radius: 6px; margin-right: 12px; margin-top: 3px; }
  .page-name { font-size: 16px; font-weight: 700; color: var(--link-blue); line-height: 1.1; }
  .page-liked { font-size: 11.5px; color: #333333; margin-top: 6px; }
  .page-liked a { color: var(--link-blue); text-decoration: none; margin-left: 4px; }
  .like-count { padding: 6px 11px 4px; font-size: 12px; color: #333333; }
  .like-count b { font-weight: 700; }
  .fans { display: grid; grid-template-columns: repeat(5, 52px); column-gap: 5.5px; row-gap: 5px; padding: 0 10px; }
  .fan { text-align: center; font-size: 10.5px; color: #666666; white-space: nowrap; }
  .fan-photo { width: 52px; height: 52px; margin-bottom: 3px; }
  .fan:nth-child(1) .fan-photo { background: linear-gradient(#b38a6c, #6d4a38); }
  .fan:nth-child(2) .fan-photo { background: linear-gradient(#e8e6e3, #8d8076); }
  .fan:nth-child(3) .fan-photo { background: linear-gradient(#a9b39c, #4d5a44); }
  .fan:nth-child(4) .fan-photo { background: linear-gradient(#3f5f7e, #0f1a28); }
  .fan:nth-child(5) .fan-photo { background: linear-gradient(#6f8a7a, #3c4a3e); }
  .fan:nth-child(6) .fan-photo { background: linear-gradient(#f16a6f, #d92f3c); }
  .fan:nth-child(7) .fan-photo { background: linear-gradient(#e4c59a, #b07a4c); }
  .fan:nth-child(8) .fan-photo { background: linear-gradient(#c29b6c, #3b2a1e); }
  .fan:nth-child(9) .fan-photo { background: linear-gradient(#7a6a52, #221a12); }
  .fan:nth-child(10) .fan-photo { background: linear-gradient(#c6b6a0, #6e5a46); }
  .fan:first-child span { color: var(--link-blue); }
  .like-box-foot { position: absolute; left: 10px; bottom: 6px; display: flex; align-items: center;
    font-size: 10.5px; color: #777777; }
  .like-box-foot i { display: inline-block; width: 12px; height: 12px; background: var(--widget-bar); margin-right: 6px; }

  /* Footer */
  .site-footer { position: absolute; left: 0; top: 996px; width: 1200px; height: 175px; background: var(--footer-bg); }
  .footer-nav { position: absolute; left: 75px; top: 36px; font-size: 18px; color: #333333; }
  .footer-nav a { color: #333333; text-decoration: none; }
  .footer-nav .sep { margin: 0 13px; color: #555555; }
  .copyright { position: absolute; left: 75px; top: 73px; font-size: 13px; color: #333333; }
  .payment-methods { position: absolute; left: 734px; top: 42px; display: flex; gap: 4px; }
  .payment-methods span { height: 26px; padding: 0 6px; display: flex; align-items: center;
    background: #ffffff; border: 1px solid #8a9bb8; font-size: 11px; font-weight: 600; color: #1d3a7a; }
  .payment-methods .coinvey { padding: 0 10px; font-size: 13px; }
  .guarantee-seal { position: absolute; left: 982px; top: 14px; }
</style>
</head>
<body>
<div class="page">

  <header class="site-header">
    <div class="brand">E-book</div>
    <div class="search">
      <span>Search here..</span>
      <svg width="20" height="20" viewBox="0 0 20 20" aria-hidden="true">
        <circle cx="8" cy="8" r="6" fill="none" stroke="#9a9a9a" stroke-width="3"/>
        <line x1="12.5" y1="12.5" x2="18" y2="18" stroke="#9a9a9a" stroke-width="3.4" stroke-linecap="round"/>
      </svg>
    </div>
    <nav class="main-nav">
      <a href="#">Main</a><a href="#">About</a><a href="#">Buy Now</a><a href="#">Video</a><a href="#">Contact</a>
    </nav>
  </header>

  <section class="hero">
    <svg class="hero-band" width="1200" height="640" viewBox="0 0 1200 640" aria-hidden="true">
      <defs>
        <linearGradient id="skyBand" x1="0" y1="0" x2="0" y2="1">
          <stop offset="0" stop-color="#66d6fd"/>
          <stop offset="0.55" stop-color="#36b6ea"/>
          <stop offset="1" stop-color="#1597d2"/>
        </linearGradient>
      </defs>
      <polygon points="0,128 1200,150 1200,596 0,623" fill="url(#skyBand)"/>
    </svg>

    <div class="title-panel">
      <div class="title-lead">Whispers from</div>
      <div class="title-main">the Back Office</div>
      <p class="title-sub">Uncover the trade tricks advisers bill huge fees<br>every season for and would rather keep hidden</p>
    </div>

    <div class="video-frame">
      <div class="video-screen">
        <div class="video-still" role="img" aria-label="Promotional video still: dark silhouette of the presenter"></div>
        <svg class="play-button" width="46" height="46" viewBox="0 0 46 46" aria-label="Play video on ClipNest">
          <circle cx="23" cy="23" r="21" fill="#2b2b2b" stroke="#ffffff" stroke-width="3"/>
          <polygon points="18,14 32,23 18,32" fill="#ffffff"/>
        </svg>
      </div>
    </div>
  </section>

  <main class="intro">
    <h1>Welcome to Our Website Mainpage</h1>
    <div class="author-photo" role="img" aria-label="Portrait photo of the author in a suit"></div>
    <div class="intro-body">
      <h2>Mauris vel lacus vitae felis vestibulum volutpat.</h2>
      <p>Etiam est nunc, venenatis in, tristique eu, imperdiet ac, nisl. Cum sociis natoque penatibus et magnis dis parturient montes, nascetur ridiculus mus. In iaculis facilisis massa. Etiam eu urna. Sed porta. Suspendisse quam leo, molestie sed, luctus quis, feugiat in, pede. Fusce tellus.</p>
      <p>Sed metus augue, convallis et, vehicula ut, pulvinar eu, ante. Integer orci tellus, tristique vitae, consequat nec, porta vel, lectus.</p>
    </div>
    <p class="intro-more">Curabitur vel mi sit amet magna malesuada ultrices. Ut nisi erat, fermentum vel, congue id, euismod in, elit. Fusce ultricies, orci ac feugiat suscipit, leo massa sodales velit, et scelerisque mi tortor at ipsum.</p>
  </main>

  <aside class="like-box">
    <div class="like-box-head">Find us on Friendloop</div>
    <div class="like-page">
      <div class="page-icon" role="img" aria-label="Page avatar"></div>
      <div>
        <div class="page-name">Pagecraft Kits</div>
        <div class="page-liked">You like this.<a href="#">Unlike</a></div>
      </div>
    </div>
    <div class="like-count">3,720 people like <b>Pagecraft Kits</b>.</div>
    <div class="fans">
      <div class="fan"><div class="fan-photo" role="img" aria-label="Fan profile photo"></div><span>Lena</span></div>
      <div class="fan"><div class="fan-photo" role="img" aria-label="Fan profile photo"></div><span>Fenna</span></div>
      <div class="fan"><div class="fan-photo" role="img" aria-label="Fan profile photo"></div><span>Shiven</span></div>
      <div class="fan"><div class="fan-photo" role="img" aria-label="Fan profile photo"></div><span>Bo</span></div>
      <div class="fan"><div class="fan-photo" role="img" aria-label="Fan profile photo"></div><span>Rovan</span></div>
      <div class="fan"><div class="fan-photo" role="img" aria-label="Fan profile photo"></div><span>Kaori</span></div>
      <div class="fan"><div class="fan-photo" role="img" aria-label="Fan profile photo"></div><span>Minh</span></div>
      <div class="fan"><div class="fan-photo" role="img" aria-label="Fan profile photo"></div><span>Mateo</span></div>
      <div class="fan"><div class="fan-photo" role="img" aria-label="Fan profile photo"></div><span>Konstantin</span></div>
      <div class="fan"><div class="fan-photo" role="img" aria-label="Fan profile photo"></div><span>Marta Delis</span></div>
    </div>
    <div class="like-box-foot"><i></i>Friendloop social plugin</div>
  </aside>

  <footer class="site-footer">
    <nav class="footer-nav">
      <a href="#">Main</a><span class="sep">/</span><a href="#">About</a><span class="sep">/</span><a href="#">Buy Now</a><span class="sep">/</span><a href="#">Video</a><span class="sep">/</span><a href="#">Contact</a>
    </nav>
    <p class="copyright">© 2013 Company Name.&nbsp; All right reserved.&nbsp; Term of Use</p>
    <div class="payment-methods">
      <span>Zelvane</span><span>Orbisca</span><span>Tamrick</span><span class="coinvey">Coinvey</span>
    </div>
    <svg class="guarantee-seal" width="122" height="122" viewBox="0 0 122 122" role="img" aria-label="100% money back guarantee seal">
      <circle cx="61" cy="61" r="58" fill="var(--gold)"/>
      <circle cx="61" cy="61" r="44" fill="var(--gold-deep)"/>
      <circle cx="61" cy="61" r="38" fill="var(--gold)"/>
    </svg>
  </footer>

</div>
</body>
</html>
```